Emerging Ed-Tech Startup seeking Stationery Designs!

We are in need of basic set of stationery designs to be used for our business operations, letters, emails, and in-office materials. We are a technology startup enhancing on campus work experience offerings by establishing a collaborative work environment for the completion of such tasks.

Our colors are Vibrant Tiffany Blue/Black/White.

Website: www.campusnorthway.com (Still under construction aside from the landing pages)

Please make sure the designs use a brighter more vibrant tiffany blue color than seen in the image files uploaded. We are not using those materials.

Our logo has been added as a file as well, please use that for any designs (include that logo). Thank you.

```html
<!DOCTYPE html>
<html lang="en">
<head>
<meta charset="utf-8">
<title>Campus Northway Stationery</title>
<link href="https://fonts.googleapis.com/css2?family=Open+Sans:wght@400;700&display=swap" rel="stylesheet">
<style>
  :root {
    --tiffany: #66ffd6;
    --ink: #1a1a1a;
    --paper: #ffffff;
    --paper-shade: #ececec;
    --flap-grey: #b9b9b9;
    --faint: #efefef;
    --backdrop: #6e4424;
    --label: #ffffff;
  }
  * { margin: 0; padding: 0; box-sizing: border-box; }
  html, body { width: 1200px; height: 540px; overflow: hidden; }
  body {
    background: var(--backdrop);
    font-family: "Open Sans", Arial, sans-serif;
    color: var(--ink);
    position: relative;
  }
  .sheet, .envelope, .card { position: absolute; background: var(--paper); overflow: hidden; }
  .letterhead { top: 32px; width: 337px; height: 436px; }
  .letterhead--plain { left: 24px; }
  .letterhead--fax { left: 398px; background: linear-gradient(160deg, #ffffff 0%, var(--paper-shade) 100%); }

  .brand { position: absolute; display: flex; align-items: center; gap: 4px; font-weight: 700; color: var(--ink); line-height: 1; letter-spacing: 0.02em; }
  .brand__mark { background: var(--tiffany); flex: none; }
  .brand__name { display: block; text-transform: uppercase; }
  .letterhead .brand { left: 10px; top: 12px; }
  .letterhead .brand__mark { width: 16px; height: 16px; }
  .letterhead .brand__name { font-size: 11px; }

  .contact { position: absolute; list-style: none; border-left: 1px solid #777; padding-left: 4px; font-size: 5.4px; line-height: 8px; }
  .contact li { display: flex; align-items: center; gap: 3px; }
  .contact li::before { content: ""; width: 4px; height: 4px; border-radius: 50%; background: var(--ink); }
  .letterhead .contact { left: 245px; top: 14px; }

  .faint-square { position: absolute; background: var(--faint); }
  .letterhead--plain .faint-square { left: 82px; top: 200px; width: 200px; height: 190px; }

  .wave { position: absolute; left: 0; bottom: 0; width: 100%; }
  .letterhead .wave { height: 92px; }

  .address { position: absolute; color: var(--paper); font-size: 6.4px; line-height: 8px; }
  .letterhead .address { right: 64px; bottom: 4px; }

  .fax-title { position: absolute; left: 26px; top: 94px; font-size: 19px; font-weight: 400; line-height: 24px; }
  .fax-fields { position: absolute; left: 26px; top: 122px; width: 288px; }
  .fax-row { display: flex; border-bottom: 1px solid #555; height: 18px; align-items: flex-end; font-size: 5.6px; padding-bottom: 1px; }
  .fax-row span { width: 172px; }
  .fax-options { position: absolute; left: 26px; top: 212px; width: 300px; display: flex; justify-content: space-between; list-style: none; font-size: 5.6px; }
  .fax-options li { display: flex; align-items: center; gap: 3px; }
  .fax-options li::before { content: ""; width: 7px; height: 7px; border: 1px solid #333; }

  .envelope { width: 377px; height: 168px; }
  .envelope--back { left: 790px; top: 34px; box-shadow: 0 1px 3px rgba(0,0,0,.4); }
  .envelope--middle { left: 778px; top: 106px; height: 170px; box-shadow: 0 1px 3px rgba(0,0,0,.4); }
  .envelope--front { left: 752px; top: 192px; height: 168px; box-shadow: 0 1px 3px rgba(0,0,0,.4); }
  .flap { position: absolute; left: 0; top: 0; width: 100%; height: 70px; }
  .envelope--front .brand { left: 8px; top: 8px; }
  .envelope--front .brand__mark { width: 12px; height: 12px; }
  .envelope--front .brand__name { font-size: 8.5px; }
  .envelope--front .return-address { position: absolute; left: 8px; top: 38px; font-size: 4.6px; line-height: 6px; }
  .envelope--front .faint-square { left: 215px; top: 40px; width: 90px; height: 80px; }
  .envelope--front .wave { height: 80px; }
  .envelope--front .web { position: absolute; right: 76px; bottom: 5px; color: var(--paper); font-size: 6.6px; line-height: 9px; }

  .card { width: 139px; height: 80px; }
  .card--front { left: 773px; top: 390px; }
  .card--back { left: 918px; top: 392px; background: var(--tiffany); }
  .card--front .brand { left: 6px; top: 18px; }
  .card--front .brand__mark { width: 10px; height: 10px; }
  .card--front .brand__name { font-size: 7px; }
  .card--front .contact { left: 72px; top: 16px; font-size: 3.4px; line-height: 5px; }
  .card--front .contact li::before { width: 2.5px; height: 2.5px; }
  .card--front .street { position: absolute; left: 72px; top: 4px; font-size: 3.4px; line-height: 4.4px; }
  .card--front .wave { height: 28px; }
  .card--front .address { right: 24px; bottom: 1.5px; font-size: 3.4px; line-height: 4.4px; }
  .card--back .brand { left: 0; right: 0; top: 18px; justify-content: center; color: var(--paper); }
  .card--back .brand__mark { width: 12px; height: 12px; background: var(--paper); }
  .card--back .brand__name { font-size: 10px; }
  .card--back .web { position: absolute; left: 0; right: 0; top: 62px; text-align: center; font-size: 5px; color: var(--ink); }

  .option-label { position: absolute; top: 484px; font-size: 24px; color: var(--label); }
  .option-label--one { left: 120px; }
  .option-label--two { left: 526px; }
</style>
</head>
<body>

<svg width="0" height="0" style="position:absolute" aria-hidden="true">
  <defs>
    <g id="swoosh">
      <path d="M0,12 C5,26 25,28 45,25 C70,20 88,20 100,27 L100,30 L0,30 Z" fill="var(--tiffany)"/>
      <path d="M0,0 C2,18 20,24 45,21 C70,16.5 88,16 100,24 L100,26 C88,18.5 70,18.5 45,23.5 C22,27 3,22 0,8 Z" fill="var(--ink)"/>
    </g>
  </defs>
</svg>

<section class="sheet letterhead letterhead--plain">
  <div class="brand"><span class="brand__mark"></span><span class="brand__name">Campus<br>Northway</span></div>
  <ul class="contact">
    <li>+91 20 4417208</li>
    <li>+91 20 5582913</li>
    <li>hello@campusnorthway.com</li>
    <li>www.campusnorthway.com</li>
  </ul>
  <div class="faint-square"></div>
  <svg class="wave" viewBox="0 0 100 30" preserveAspectRatio="none"><use href="#swoosh"/></svg>
  <p class="address">Street Name, City Name<br>State Zipcode</p>
</section>

<section class="sheet letterhead letterhead--fax">
  <div class="brand"><span class="brand__mark"></span><span class="brand__name">Campus<br>Northway</span></div>
  <ul class="contact">
    <li>+91 20 4417208</li>
    <li>+91 20 5582913</li>
    <li>hello@campusnorthway.com</li>
    <li>www.campusnorthway.com</li>
  </ul>
  <h1 class="fax-title">FAX</h1>
  <div class="fax-fields">
    <div class="fax-row"><span>To :</span>From :</div>
    <div class="fax-row"><span>Fax :</span>Pages :</div>
    <div class="fax-row"><span>Phone :</span>Date :</div>
    <div class="fax-row"><span>Re :</span>CC :</div>
  </div>
  <ul class="fax-options">
    <li>Urgent</li><li>For Review</li><li>Please Comment</li><li>Please Reply</li><li>Please Recycle</li>
  </ul>
  <svg class="wave" viewBox="0 0 100 30" preserveAspectRatio="none"><use href="#swoosh"/></svg>
  <p class="address">Street Name, City Name<br>State Zipcode</p>
</section>

<section class="envelope envelope--back">
  <svg class="flap" viewBox="0 0 377 70" preserveAspectRatio="none"><path d="M0,0 H377 L340,40 Q330,48 300,52 L200,68 Q188,70 176,68 L77,52 Q47,48 37,40 Z" fill="var(--flap-grey)"/></svg>
</section>

<section class="envelope envelope--middle">
  <svg class="flap" viewBox="0 0 377 70" preserveAspectRatio="none"><path d="M0,0 H377 L340,40 Q330,48 300,52 L200,68 Q188,70 176,68 L77,52 Q47,48 37,40 Z" fill="var(--tiffany)"/></svg>
</section>

<section class="envelope envelope--front">
  <div class="brand"><span class="brand__mark"></span><span class="brand__name">Campus<br>Northway</span></div>
  <p class="return-address">Street Name, City Name<br>State Zipcode</p>
  <div class="faint-square"></div>
  <svg class="wave" viewBox="0 0 100 30" preserveAspectRatio="none"><use href="#swoosh"/></svg>
  <p class="web">www.hollisford.com</p>
</section>

<section class="card card--front">
  <div class="brand"><span class="brand__mark"></span><span class="brand__name">Campus<br>Northway</span></div>
  <p class="street">Street Name, City Name<br>State Zipcode</p>
  <ul class="contact">
    <li>+91 20 4417208</li>
    <li>+91 20 5582913</li>
    <li>hello@campusnorthway.com</li>
    <li>www.campusnorthway.com</li>
  </ul>
  <svg class="wave" viewBox="0 0 100 30" preserveAspectRatio="none"><use href="#swoosh"/></svg>
  <p class="address">Street Name City</p>
</section>

<section class="card card--back">
  <div class="brand"><span class="brand__mark"></span><span class="brand__name">Campus<br>Northway</span></div>
  <p class="web">www.campusnorthway.com</p>
</section>

<p class="option-label option-label--one">Option-1</p>
<p class="option-label option-label--two">Option-2</p>

</body>
</html>
```